Moravel Aesthetic Doctor

I require an elegant, luxurious looking business card for my aesthetic business. I am a doctor and that will set me aside from competitors. I am planning to provide home and spa based treatments to clients with high expectations. I have attached my logo.

```html
<!DOCTYPE html>
<html lang="en">
<head>
<meta charset="utf-8">
<title>Moravel Aesthetic Doctor – Business Card</title>
<link href="https://fonts.googleapis.com/css2?family=Raleway:wght@400;500&family=Roboto:wght@400;500&display=swap" rel="stylesheet">
<style>
  :root{
    --bg:#5a5a5c;
    --card-dark:#2e2e30;
    --card-light:#ffffff;
    --sky:#5bbde8;
    --grey-text:#8c8c8e;
    --rule:#9a9a9a;
    --white:#f4f4f4;
  }
  *{box-sizing:border-box;margin:0;padding:0}
  html,body{width:1200px;height:1124px;overflow:hidden}
  body{background:var(--bg);font-family:"Raleway",sans-serif;position:relative}
  .card{position:absolute;left:170px;width:860px;height:491px;overflow:hidden;box-shadow:0 12px 30px rgba(0,0,0,.35)}
  .card--front{top:50px;background:var(--card-dark);border-left:5px solid var(--sky);border-bottom:5px solid var(--sky)}
  .card--back{top:583px;background:var(--card-light);border-left:5px solid var(--sky);border-bottom:5px solid var(--sky)}

  .portrait-area{position:absolute;left:40px;top:60px;width:400px;height:400px;border-radius:50%;
    background:radial-gradient(circle at 55% 40%,#6a6a6c 0%,#3d3d3f 55%,#2a2a2c 100%);
    border:4px solid #555557}

  .brand{position:absolute;font-family:"Raleway",sans-serif;font-weight:400;letter-spacing:.06em;line-height:1.05}
  .card--front .brand{right:44px;top:42px;color:var(--white);font-size:38px;text-align:left}
  .brand span{display:block}
  .brand .brand-sub{font-size:20px;letter-spacing:.14em;margin-top:4px}

  .services{position:absolute;left:520px;top:165px;list-style:none;color:var(--white);font-size:22px;line-height:1.45}
  .services li{position:relative;padding-left:20px}
  .services li::before{content:"";position:absolute;left:0;top:13px;width:8px;height:8px;border-radius:50%;background:var(--sky)}
  .services li.cont::before{display:none}

  .card--back .brand{right:60px;top:80px;color:var(--grey-text);font-size:52px;display:flex;align-items:center;gap:22px}
  .brand-dot{width:70px;height:70px;border-radius:50%;background:var(--sky);flex:none}
  .card--back .brand .brand-sub{font-size:24px}

  .person{position:absolute;left:110px;top:215px;right:90px}
  .person-name{font-family:"Roboto",sans-serif;font-weight:500;font-size:32px;color:var(--sky)}
  .person-name small{font-size:18px;margin-left:4px}
  .person-title{font-size:22px;color:var(--grey-text);margin-top:4px;padding-bottom:14px;border-bottom:2px solid var(--rule)}

  .contacts{position:absolute;left:90px;top:330px;list-style:none;font-family:"Roboto",sans-serif;font-size:23px;color:var(--grey-text)}
  .contacts li{display:flex;align-items:center;gap:16px;margin-bottom:6px}
  .contacts svg{width:22px;height:22px;flex:none}
  .contacts .accent{color:var(--sky)}

  .social{position:absolute;right:60px;bottom:40px;display:flex;gap:26px}
  .social span{width:28px;height:28px;border-radius:50%;background:var(--sky)}
</style>
</head>
<body>

<section class="card card--front">
  <div class="portrait-area" role="img" aria-label="Illustration of a woman's profile with flowing hair inside a circle"></div>
  <div class="brand">
    <span>Moravel</span>
    <span class="brand-sub">Aesthetic Doctor</span>
  </div>
  <ul class="services">
    <li>Dermal injectables</li>
    <li>Plasma facials</li>
    <li>Microneedling</li>
    <li>Skin boosters</li>
    <li>Excessive sweating</li>
    <li>Home and Spa Based</li>
    <li class="cont">Treatments</li>
  </ul>
</section>

<section class="card card--back">
  <div class="brand">
    <div class="brand-dot"></div>
    <div>
      <span>Moravel</span>
      <span class="brand-sub">Aesthetic Doctor</span>
    </div>
  </div>

  <div class="person">
    <p class="person-name">Dr Lena Varga, <small>MRCPCH MD</small></p>
    <p class="person-title">Australasian Diploma of Aesthetic Medicine</p>
  </div>

  <ul class="contacts">
    <li>
      <svg viewBox="0 0 24 24"><path fill="#5bbde8" d="M6.6 10.8a15 15 0 0 0 6.6 6.6l2.2-2.2a1 1 0 0 1 1-.25 11.4 11.4 0 0 0 3.6.57 1 1 0 0 1 1 1V20a1 1 0 0 1-1 1A17 17 0 0 1 3 4a1 1 0 0 1 1-1h3.5a1 1 0 0 1 1 1c0 1.25.2 2.45.57 3.57a1 1 0 0 1-.25 1z"/></svg>
      0800 555 019
    </li>
    <li>
      <svg viewBox="0 0 24 24" fill="none" stroke="#5bbde8" stroke-width="2"><rect x="2" y="5" width="20" height="14" rx="1"/><path d="M2 6l10 7 10-7"/></svg>
      lena@moravel.co.nz
    </li>
    <li>
      <svg viewBox="0 0 24 24" fill="none" stroke="#5bbde8" stroke-width="1.8"><circle cx="12" cy="12" r="10"/><ellipse cx="12" cy="12" rx="4.5" ry="10"/><path d="M2 12h20M4 7h16M4 17h16"/></svg>
      <span>www.<span class="accent">moravel</span>.co.nz</span>
    </li>
  </ul>

  <div class="social"><span></span><span></span></div>
</section>

</body>
</html>
```